Request for Business Card Design

Hi. My name is Marlene, I am looking for a new business card design for my company, Quarrow Signal Instruments, LLC. I really like the design you did for Tarsel Venture and was hoping you could do something similar using our full logo and our mark. I am also open to any raised texture design using our mark. I have attached our full logo, which would need to be somewhere on the card, as well as the mark in both outline and full form, as well as our brand colors / guide. The card does not have to be white, as long as our logo and mark appear. I actually like darker colored business cards more, but am open to all options. If you are interested in working with me, please let me know. We would also take the business card design into letterhead design if you can do that.

```html
<!DOCTYPE html>
<html lang="en">
<head>
<meta charset="utf-8">
<title>Quarrow Signal Instruments – Business Card</title>
<link rel="stylesheet" href="https://fonts.googleapis.com/css2?family=Barlow+Semi+Condensed:wght@600&family=Montserrat:wght@400;700&display=swap">
<style>
  :root {
    --brand-blue: #0b9ac1;
    --ink-gray: #3d3f42;
    --paper: #ffffff;
    --stage: #2b2b2d;
  }
  * { margin: 0; padding: 0; box-sizing: border-box; }
  html, body { width: 1200px; height: 880px; overflow: hidden; background: var(--stage); }
  .canvas { position: relative; width: 1200px; height: 880px; }

  .card {
    position: absolute;
    width: 600px; height: 343px;
    overflow: hidden;
    box-shadow: 0 10px 28px rgba(0,0,0,.45);
  }
  .card-front { left: 110px; top: 70px; background: var(--brand-blue); }
  .card-back  { left: 490px; top: 467px; background: var(--paper); }

  .wordmark {
    position: absolute;
    display: flex; align-items: center; gap: 14px;
    font-family: "Barlow Semi Condensed", sans-serif;
    font-weight: 600;
  }
  .wordmark-dot { border-radius: 50%; flex: none; }
  .wordmark-text { display: flex; flex-direction: column; line-height: 1; }
  .wordmark-main { letter-spacing: .08em; }
  .wordmark-sub  { letter-spacing: .04em; margin-top: 4px; }

  .card-front .wordmark { left: 120px; top: 130px; color: var(--paper); }
  .card-front .wordmark-dot { width: 58px; height: 58px; background: var(--paper); }
  .card-front .wordmark-main { font-size: 54px; }
  .card-front .wordmark-sub  { font-size: 15.5px; }

  .card-back .wordmark { left: 44px; top: 110px; color: var(--ink-gray); }
  .card-back .wordmark-dot { width: 38px; height: 38px; background: var(--brand-blue); }
  .card-back .wordmark-main { font-size: 36px; }
  .card-back .wordmark-sub  { font-size: 10.5px; }

  .wave { position: absolute; inset: 0; }

  .contact {
    position: absolute; right: 26px; top: 96px;
    text-align: right; color: var(--paper);
    font-family: "Montserrat", sans-serif; font-size: 11.5px; line-height: 1.45;
  }
  .contact-name { font-weight: 700; font-size: 14px; letter-spacing: .02em; }
  .contact-role { margin-bottom: 12px; }
  .contact-address { margin-bottom: 8px; }
  .contact-line { display: flex; justify-content: flex-end; align-items: center; gap: 6px; }
  .contact-line svg { width: 11px; height: 11px; fill: var(--paper); flex: none; }
</style>
</head>
<body>
<main class="canvas">

  <section class="card card-front" aria-label="Card front">
    <div class="wordmark">
      <span class="wordmark-dot"></span>
      <span class="wordmark-text">
        <span class="wordmark-main">QUARROW</span>
        <span class="wordmark-sub">SIGNAL INSTRUMENTS</span>
      </span>
    </div>
  </section>

  <section class="card card-back" aria-label="Card back">
    <svg class="wave" viewBox="0 0 600 343" width="600" height="343" aria-hidden="true">
      <defs>
        <path id="wave-edge" d="M545,-40 L520,0 C440,20 410,70 385,120 C360,175 335,240 270,262 C200,285 100,282 0,282 L-60,300 L-60,400 L700,400 L700,-40 Z"/>
      </defs>
      <use href="#wave-edge" fill="var(--brand-blue)" transform="translate(-30,-14)"/>
      <use href="#wave-edge" fill="var(--paper)" transform="translate(-26,-12)"/>
      <use href="#wave-edge" fill="var(--ink-gray)" transform="translate(-22,-10)"/>
      <use href="#wave-edge" fill="var(--paper)" transform="translate(-5,-2)"/>
      <use href="#wave-edge" fill="var(--brand-blue)"/>
    </svg>

    <div class="wordmark">
      <span class="wordmark-dot"></span>
      <span class="wordmark-text">
        <span class="wordmark-main">QUARROW</span>
        <span class="wordmark-sub">SIGNAL INSTRUMENTS</span>
      </span>
    </div>

    <div class="contact">
      <p class="contact-name">DORIAN VALE</p>
      <p class="contact-role">Owner</p>
      <p class="contact-address">482 Fernhollow Ave, Ste<br>200, Brackton, TX 75890</p>
      <p class="contact-line">555.014.2290
        <svg viewBox="0 0 24 24"><path d="M6.6 10.8a15.1 15.1 0 0 0 6.6 6.6l2.2-2.2a1 1 0 0 1 1-.25 11.4 11.4 0 0 0 3.6.57 1 1 0 0 1 1 1V20a1 1 0 0 1-1 1A17 17 0 0 1 3 4a1 1 0 0 1 1-1h3.5a1 1 0 0 1 1 1c0 1.250.2 2.450.57 3.570a1 1 0 0 1-.25 1z"/></svg>
      </p>
      <p class="contact-line">info@quarrowsignal.com
        <svg viewBox="0 0 24 24"><path d="M2 5h20v14H2z M3 6l9 7 9-7" fill="none" stroke="#fff" stroke-width="2"/></svg>
      </p>
      <p class="contact-line">www.quarrowsignal.com
        <svg viewBox="0 0 24 24"><circle cx="12" cy="12" r="9" fill="none" stroke="#fff" stroke-width="2"/><path d="M3 12h18M12 3c3 3 3 15 0 18M12 3c-3 3-3 15 0 18" fill="none" stroke="#fff" stroke-width="1.6"/></svg>
      </p>
    </div>
  </section>

</main>
</body>
</html>
```